International oil and gas consultancy business needs a web design

Hello, I need a web design for a new oil and gas auditing consultancy business. My business undertakes contract audit assignments to review past costs of oil and gas operations (see attached Excel file for more details of the businesses services). I need the design to give the impression of a professional consultancy style of business, rather than a retail style of website. Note: this job is for LAYOUT DESIGN ONLY and not coding / development work.
The following are my key design principles:
1. BASIC DESIGN: I am after a simple and static web design. I don't want the pages busy or cluttered with too many images or detail.
2. HORIZONTAL TABS: I require a horizontal set of tabs towards the top of the screens (see Excel file) which remain in the same position on every page.
3. META TAG PLANNING: The design should allow for effective positioning of content so that key meta tag words can easily be built during the technical build stage.
4. NUMBER OF PAGES: The site will eventually have a maximum of 10 pages. Seven of the pages will reside under the tabs. Can you please present your opening submission for the first two page.
5. USE OF MY LOGO: The attached logo (JPEG file) should be used throughout the website. Please don't change the shape and colour.
6. COLOUR SCHEMES: Can you please consider any of the 3 colour schemes below:
A - dark red (to match the logo), light grey and perhaps another of your liking;
B - dark red (to match the logo), light cream and perhaps another of your liking;
C - dark red (to match the logo), white and perhaps another of your liking.
7. WORD CONTENT: I have attached an Excel file which shows the estimated word content for each page.
8. FUTURE USE OF DESIGN: I'm planning on building a Wordpress website. Can you please ensure the layout design supports this application.

Target Market(s)

oil and gas companies (small and large)

Industry/Entity Type

Oil And Gas

Font styles to use
Sans Serif

Requirements
Nice to have
• The KRL logo and business name should ideally be next to each other. Also, the logo and name should be part of the background graphics, not above it.

```html
<!DOCTYPE html>
<html lang="en">
<head>
<meta charset="utf-8">
<title>Kestrel Ridge Auditing</title>
<link href="https://fonts.googleapis.com/css2?family=Roboto:wght@300;400;500;700&display=swap" rel="stylesheet">
<style>
:root{
  --red:#9b1d22;
  --red-dark:#7e1418;
  --red-nav-top:#b0373a;
  --red-nav-bottom:#8c1c20;
  --home-grey:#4a4a4a;
  --ink:#333333;
  --muted:#444444;
  --search-bg:#e6e6e6;
  --footer:#2e2e2e;
  --white:#ffffff;
}
*{box-sizing:border-box;margin:0;padding:0}
html,body{width:954px;height:1200px;overflow:hidden;background:var(--white);font-family:'Roboto',Arial,sans-serif;color:var(--ink)}
.page{position:relative;width:954px;height:1200px}

.site-header{position:absolute;left:0;top:0;width:954px;height:83px}
.brand{position:absolute;left:80px;top:21px;display:flex;align-items:center;gap:9px}
.brand-mark{width:16px;height:16px;background:var(--red)}
.brand-name{font-weight:700;font-size:42px;color:var(--red);letter-spacing:1px;line-height:1}
.search{position:absolute;left:594px;top:27px;width:166px;height:30px;background:var(--search-bg);font-size:10px;color:#333;padding:10px 0 0 12px}
.search svg{position:absolute;right:10px;top:8px}
.social-top{position:absolute;left:771px;top:27px;display:flex;gap:4px}
.social-top span{width:31px;height:31px;border-radius:3px;display:block;box-shadow:inset 0 -10px 14px rgba(0,0,0,.18),inset 0 1px 0 rgba(255,255,255,.35)}
.social-top .s1{background:#55aee6}
.social-top .s2{background:#3b5c9a}
.social-top .s3{background:#3a3a3a}

.main-nav{position:absolute;left:0;top:83px;width:954px;height:50px;background:linear-gradient(var(--red-nav-top),var(--red-nav-bottom))}
.main-nav ul{list-style:none;display:flex;position:absolute;left:79px;top:0;height:50px}
.main-nav li{height:50px;display:flex;align-items:center;padding:0 14px;color:var(--white);font-size:15px;text-transform:uppercase;border-right:1px solid rgba(0,0,0,.25)}
.main-nav li.active{background:var(--home-grey);padding:0 21px;border-right:none}
.main-nav li:last-child{border-right:none}

.hero{position:absolute;left:0;top:134px;width:954px;height:441px;
  background:
    radial-gradient(ellipse 180px 240px at 320px 200px,rgba(160,185,215,.55),transparent 70%),
    radial-gradient(ellipse 200px 220px at 520px 280px,rgba(185,150,125,.45),transparent 70%),
    radial-gradient(ellipse 220px 120px at 130px 420px,rgba(60,60,60,.35),transparent 70%),
    linear-gradient(100deg,#d4d4d4 0%,#eceeef 30%,#dfe3e9 50%,#e6ddd6 62%,#eeeff1 80%,#f5f5f5 100%)}
.hero-caption{position:absolute;left:477px;top:259px;width:398px;height:90px;background:rgba(90,90,90,.72);color:var(--white);text-align:center;padding-top:12px}
.hero-caption h1{font-weight:400;font-size:32px;line-height:1.2}
.hero-caption p{font-size:16px;margin-top:3px}
.hero-dots{position:absolute;left:913px;top:26px;display:flex;flex-direction:column;gap:5px}
.hero-dots span{width:10px;height:10px;border-radius:50%;background:#666}
.hero-dots span:first-child{background:var(--red)}

.welcome{position:absolute;left:0;top:575px;width:954px;height:156px;background:linear-gradient(#f6f8fa,#eef0f3);text-align:center}
.welcome h2{font-weight:400;font-size:17px;color:var(--red);margin-top:36px}
.welcome p{font-size:12.5px;line-height:24px;color:var(--muted);width:780px;margin:16px auto 0}

.services{position:absolute;left:0;top:731px;width:954px;height:372px}
.services h2{font-weight:400;font-size:18px;color:var(--red);text-align:center;margin-top:25px}
.service-card{position:absolute;top:76px;width:240px;text-align:center}
.service-photo{width:240px;height:136px;border:2px solid #ddd}
.service-card h3{font-weight:400;font-size:17px;color:var(--red);margin-top:12px}
.service-card p{font-size:10.5px;line-height:17.5px;color:var(--muted);margin-top:6px;text-align:justify;text-align-last:center;padding:0 3px}
.btn{display:inline-block;width:87px;height:31px;line-height:31px;margin-top:13px;background:linear-gradient(#a32a2e,var(--red-dark));color:var(--white);font-size:12.5px;border-radius:2px}

.site-footer{position:absolute;left:0;top:1103px;width:954px;height:97px;background:var(--footer);color:var(--white);font-size:12px}
.copyright{position:absolute;left:82px;top:42px}
.footer-social{position:absolute;left:420px;top:35px;display:flex;gap:6px}
.footer-social span{width:24px;height:24px;border-radius:50%;background:var(--white);box-shadow:inset 0 0 0 3px #fff,inset 0 0 0 4px #bdbdbd}
.footer-links{position:absolute;right:82px;top:40px}
</style>
</head>
<body>
<div class="page">
  <header class="site-header">
    <div class="brand"><span class="brand-mark"></span><span class="brand-name">KRL</span></div>
    <div class="search">Search...
      <svg width="14" height="14" viewBox="0 0 14 14"><circle cx="5.5" cy="5.5" r="4.2" fill="none" stroke="#888" stroke-width="2"/><line x1="8.5" y1="8.5" x2="13" y2="13" stroke="#888" stroke-width="2.4"/></svg>
    </div>
    <div class="social-top" aria-label="Social links"><span class="s1"></span><span class="s2"></span><span class="s3"></span></div>
  </header>

  <nav class="main-nav">
    <ul>
      <li class="active">Home</li>
      <li>About Us</li>
      <li>Services</li>
      <li>Our Partners</li>
      <li>Approach</li>
      <li>Why Choose Us</li>
      <li>Contact Us</li>
    </ul>
  </nav>

  <section class="hero" role="img" aria-label="Photo of two colleagues reviewing work at an office desk">
    <div class="hero-caption">
      <h1>Kestrel Ridge Auditing</h1>
      <p>Lorem Ipsum is simply dummy text of the printing</p>
    </div>
    <div class="hero-dots"><span></span><span></span><span></span><span></span><span></span></div>
  </section>

  <section class="welcome">
    <h2>WELCOME TO KESTREL RIDGE AUDITING</h2>
    <p>Kestrel Ridge Auditing is a Perth (Australia) based firm specialising in providing quality audit services for the oil and gas industry. Our skills and knowledge of oil and gas, along with a deep understanding of business commercial needs, ensures the high quality of our services</p>
  </section>

  <section class="services">
    <h2>Kestrel Ridge Auditing specialise in the following services:</h2>
    <article class="service-card" style="left:79px">
      <div class="service-photo" role="img" aria-label="Photo of a team meeting around a table" style="background:radial-gradient(ellipse 80px 60px at 70px 95px,rgba(215,185,220,.7),transparent 70%),radial-gradient(ellipse 90px 50px at 160px 110px,rgba(170,205,215,.7),transparent 70%),linear-gradient(135deg,#e7ecf1,#d3dce5 50%,#f0f3f6)"></div>
      <h3>Joint Venture audits</h3>
      <p>Lorem Ipsum is simply dummy text of the printing and typesetting industry. Lorem Ipsum has been the industry's standard dummy text</p>
      <span class="btn">Read More</span>
    </article>
    <article class="service-card" style="left:353px">
      <div class="service-photo" role="img" aria-label="Photo of office staff discussing a contract" style="background:radial-gradient(ellipse 70px 70px at 80px 100px,rgba(225,225,230,.55),transparent 70%),radial-gradient(ellipse 60px 80px at 180px 80px,rgba(40,45,60,.6),transparent 70%),linear-gradient(135deg,#8f9297,#62656b 55%,#44474d)"></div>
      <h3>Contract audits</h3>
      <p>Lorem Ipsum is simply dummy text of the printing and typesetting industry. Lorem Ipsum has been the industry's standard dummy text</p>
      <span class="btn">Read More</span>
    </article>
    <article class="service-card" style="left:630px">
      <div class="service-photo" role="img" aria-label="Photo of colleagues looking at tablets" style="background:radial-gradient(ellipse 90px 70px at 110px 70px,rgba(215,190,160,.5),transparent 70%),radial-gradient(ellipse 70px 80px at 200px 70px,rgba(170,195,230,.7),transparent 70%),linear-gradient(135deg,#f0f2f5,#dde2e9 50%,#ccd8e8)"></div>
      <h3>Operations audits</h3>
      <p>Lorem Ipsum is simply dummy text of the printing and typesetting industry. Lorem Ipsum has been the industry's standard dummy text</p>
      <span class="btn">Read More</span>
    </article>
  </section>

  <footer class="site-footer">
    <div class="copyright">Copyright © 2014 Kestrel Ridge Audit</div>
    <div class="footer-social" aria-label="Social links"><span></span><span></span><span></span><span></span></div>
    <div class="footer-links">Terms and Conditions &nbsp;|&nbsp; Privacy policy</div>
  </footer>
</div>
</body>
</html>
```